Create a PPTX template for our business

We need a Powerpoint and Keynote template design for a new company called "Quorvell" We connect hotel guests to hotel employees through text messaging so guests can ask for what they need during their stay. The name "Quorvell" is derived from the word "Affinity" which is how we want our hotel customer's employees and their guests to feel about each other. The color palette chosen is meant to evoke feelings of "warmth" and "comfort," which is how most people feel when they have a strong affinity to each other. The "-ium" ending of Quorvell is intended to give a technological feel to our business since we use technology to connect people together.

A *.ai file is included which contains our logo.

```html
<!DOCTYPE html>
<html lang="en">
<head>
<meta charset="utf-8">
<title>Quorvell Presentation Template</title>
<link rel="stylesheet" href="https://fonts.googleapis.com/css2?family=PT+Sans+Narrow:wght@400;700&family=PT+Sans:ital,wght@0,400;1,400&display=swap">
<style>
  :root {
    --page-bg: #15191b;
    --sky-top: #e6f6f8;
    --sky-bottom: #c9edf1;
    --cream: #fbfad6;
    --teal-dark: #0f6a68;
    --teal-mid: #1e9b91;
    --teal-ring: #3fb3b5;
    --lime: #c8dd3a;
    --lime-dark: #98b022;
    --title: #126e6c;
    --body-text: #2f3f40;
    --subtext: #3f8a8a;
    --logo-text: #5a5f63;
    --ghost: #9cd4de;
  }
  * { box-sizing: border-box; margin: 0; padding: 0; }
  html, body { width: 1200px; height: 900px; overflow: hidden; }
  body { background: var(--page-bg); position: relative; font-family: "PT Sans Narrow", "Arial Narrow", sans-serif; }

  .slide {
    position: absolute; width: 586px; height: 438px; overflow: hidden;
    background: linear-gradient(180deg, var(--sky-top), var(--sky-bottom));
  }
  .slide--1 { left: 10px; top: 8px; }
  .slide--2 { left: 604px; top: 8px; }
  .slide--3 { left: 10px; top: 454px; }
  .slide--4 { left: 604px; top: 454px; }

  .ghost-mark {
    position: absolute; right: 40px; top: 60px; width: 240px; height: 240px;
    border-radius: 50%; background: var(--ghost); opacity: .35;
  }

  .slide-title {
    position: absolute; left: 28px; top: 12px; font-size: 27px; font-weight: 700; color: var(--title);
  }
  .title-flag {
    position: absolute; left: 0; top: 14px; width: 18px; height: 30px; background: var(--teal-mid);
    clip-path: polygon(0 0, 100% 0, 55% 50%, 100% 100%, 0 100%);
  }

  .footer {
    position: absolute; left: 0; bottom: 0; width: 100%; height: 44px;
    background: linear-gradient(180deg, #2fae9f, var(--teal-dark));
    border-top: 3px solid var(--lime);
  }
  .slide-number {
    position: absolute; left: 16px; top: 8px; width: 29px; height: 24px;
    background: linear-gradient(180deg, #c3d94a, var(--lime-dark));
    border: 1px solid #e2ef8a; color: #fff; font-size: 17px; text-align: center; line-height: 22px;
  }
  .footer-text {
    position: absolute; left: 63px; top: 11px; color: #fff; font-family: "PT Sans", sans-serif;
    font-style: italic; font-size: 13px;
  }
  .footer-date { left: 92px; font-style: normal; font-size: 14px; }
  .nav-button {
    position: absolute; top: 6px; height: 27px; color: #fff; font-family: "PT Sans", sans-serif;
    font-size: 12px; line-height: 27px; text-align: center;
    background: linear-gradient(180deg, #dbe860, var(--lime-dark));
  }
  .nav-button--next { right: 16px; width: 46px; border-radius: 4px; }
  .nav-button--start { right: 16px; width: 44px; border-radius: 4px; }
  .nav-button--back {
    right: 70px; width: 50px; padding-left: 8px;
    clip-path: polygon(20% 0, 100% 0, 100% 100%, 20% 100%, 0 50%);
  }

  /* title slide */
  .cover-bottom {
    position: absolute; left: 0; top: 258px; width: 100%; height: 137px;
    background: linear-gradient(180deg, var(--cream), #f4f7dc);
    border-top: 4px solid var(--lime);
  }
  .portrait-ring {
    position: absolute; left: 20px; top: 150px; width: 212px; height: 212px; border-radius: 50%;
    background: #fff; border: 5px solid var(--lime);
  }
  .portrait {
    position: absolute; left: 7px; top: 7px; width: 188px; height: 188px; border-radius: 50%;
    border: 4px solid var(--teal-ring);
    background: radial-gradient(circle at 50% 40%, #d8b49a 0%, #c59a80 30%, #e8eef0 55%, #2c3035 75%);
  }
  .project-title {
    position: absolute; right: 34px; top: 96px; font-size: 34px; font-weight: 700; color: var(--title);
  }
  .project-subtext {
    position: absolute; right: 34px; top: 141px; width: 360px; text-align: right;
    font-family: "PT Sans", sans-serif; font-size: 12.5px; line-height: 19px; color: var(--subtext);
  }
  .brand {
    position: absolute; left: 326px; top: 300px; display: flex; align-items: center; gap: 12px;
  }
  .brand-square { width: 30px; height: 30px; background: var(--teal-ring); }
  .brand-name { font-size: 38px; font-weight: 400; color: var(--logo-text); letter-spacing: 1px; }

  /* content slides */
  .section-heading {
    position: absolute; left: 44px; top: 74px; font-size: 18px; font-weight: 700; color: var(--teal-dark);
  }
  .check-list {
    position: absolute; left: 44px; top: 101px; list-style: none;
    font-size: 13px; line-height: 19px; color: var(--body-text);
  }
  .check-list li { position: relative; padding-left: 22px; }
  .check-list svg { position: absolute; left: 0; top: 3px; width: 14px; height: 14px; }
  .list--business { width: 470px; }
  .team-photo {
    position: absolute; left: 210px; top: 92px; width: 350px; height: 280px;
    background: linear-gradient(180deg, #7a7e84 0%, #5a5f66 45%, #9fa5aa 70%, rgba(201,237,241,0) 100%);
    border-radius: 40px 40px 0 0;
  }
</style>
</head>
<body>
<svg width="0" height="0" style="position:absolute">
  <defs>
    <symbol id="tick" viewBox="0 0 14 14">
      <rect x="1" y="3" width="10" height="10" fill="none" stroke="#2f3f40" stroke-width="1.3"/>
      <path d="M3 7 L6 10.5 L13 1" fill="none" stroke="#2f3f40" stroke-width="2"/>
    </symbol>
  </defs>
</svg>

<section class="slide slide--1">
  <div class="cover-bottom"></div>
  <h1 class="project-title">Project Title Here</h1>
  <p class="project-subtext">Subtext here Subtext here Subtext here Subtext here Subtext here Subtext here Subtext here Subtext here</p>
  <div class="portrait-ring"><div class="portrait" role="img" aria-label="Portrait photo of the presenter"></div></div>
  <div class="brand"><span class="brand-square"></span><span class="brand-name">QUORVELL</span></div>
  <footer class="footer">
    <span class="slide-number">01</span>
    <span class="footer-text footer-date">01/02/15</span>
    <span class="nav-button nav-button--start">Start</span>
  </footer>
</section>

<section class="slide slide--2">
  <div class="ghost-mark"></div>
  <span class="title-flag"></span>
  <h2 class="slide-title">Slide Title Presentation</h2>
  <footer class="footer">
    <span class="slide-number">02</span>
    <span class="footer-text">Tagline/Slogan about Your Company</span>
    <span class="nav-button nav-button--back">Back</span>
    <span class="nav-button nav-button--next">Next</span>
  </footer>
</section>

<section class="slide slide--3">
  <div class="ghost-mark"></div>
  <span class="title-flag"></span>
  <h2 class="slide-title">Slide Title Presentation</h2>
  <h3 class="section-heading">Something About Your Business</h3>
  <ul class="check-list list--business">
    <li><svg><use href="#tick"/></svg>High volume local boutique real estate company</li>
    <li><svg><use href="#tick"/></svg>Specialize in selling homes throughout the San Francisco Bay Area</li>
    <li><svg><use href="#tick"/></svg>Focus on modern marketing techniques and thinking outside the box</li>
    <li><svg><use href="#tick"/></svg>“High Tech and High Touch” approach to real estate</li>
    <li><svg><use href="#tick"/></svg>Certified Green Business Everything is done and stored online. No File Cabinets in our offices!</li>
    <li><svg><use href="#tick"/></svg>Exceptional web presence far beyond other local real estate companies</li>
    <li><svg><use href="#tick"/></svg>Clean, streamline, and hip marketing materials</li>
    <li><svg><use href="#tick"/></svg>A company constantly looking into the latest real estate trends, tools, and technology to better assist their agents and clients sell homes in the modern world, all while embracing tried and true real estate values and practices as well</li>
    <li><svg><use href="#tick"/></svg>Leading authority for architectural homes and recognized world wide</li>
    <li><svg><use href="#tick"/></svg>Not Just Modern Homes! We focus on Modern Real Estate<br>Practices through and through.</li>
  </ul>
  <footer class="footer">
    <span class="slide-number">03</span>
    <span class="footer-text">Tagline/Slogan about Your Company</span>
    <span class="nav-button nav-button--back">Back</span>
    <span class="nav-button nav-button--next">Next</span>
  </footer>
</section>

<section class="slide slide--4">
  <div class="ghost-mark"></div>
  <span class="title-flag"></span>
  <h2 class="slide-title">Slide Title Presentation</h2>
  <h3 class="section-heading">Our Services</h3>
  <ul class="check-list">
    <li><svg><use href="#tick"/></svg>Handymen</li>
    <li><svg><use href="#tick"/></svg>Contractors</li>
    <li><svg><use href="#tick"/></svg>Stagers</li>
    <li><svg><use href="#tick"/></svg>Painters</li>
    <li><svg><use href="#tick"/></svg>Cleaners</li>
    <li><svg><use href="#tick"/></svg>Movers</li>
    <li><svg><use href="#tick"/></svg>Storage companies</li>
    <li><svg><use href="#tick"/></svg>Landscapers</li>
    <li><svg><use href="#tick"/></svg>Estate Sale Professionals</li>
    <li><svg><use href="#tick"/></svg>Lawyers</li>
    <li><svg><use href="#tick"/></svg>Mortgage Brokers</li>
    <li><svg><use href="#tick"/></svg>Inspectors</li>
  </ul>
  <div class="team-photo" role="img" aria-label="Group photo of service professionals in business and work attire"></div>
  <footer class="footer">
    <span class="slide-number">04</span>
    <span class="footer-text">Tagline/Slogan about Your Company</span>
    <span class="nav-button nav-button--back">Back</span>
    <span class="nav-button nav-button--next">Next</span>
  </footer>
</section>
</body>
</html>
```